Maple Grove Schools | brand new stationery!

We need stationery design with our new logo! Our company updated it's name and image and we like to incorporate the new one on our stationery, business cards and email signature. We are looking for fresh, new ideas!
Industry: Childcare, Elementary and Middle School
Company Name: Maple Grove Schools
Tagline: Bright Futures Start Here
Main colors: Blue, white and a little yellow
Star shape is something new for us! Do you see a way to incorporate it as a design element?

```html
<!DOCTYPE html>
<html lang="en">
<head>
<meta charset="utf-8">
<title>Maple Grove Schools – Email Signature</title>
<link href="https://fonts.googleapis.com/css2?family=Raleway:wght@500;700&family=Roboto:wght@400;500;700&display=swap" rel="stylesheet">
<style>
  :root {
    --bg: #e6e7e9;
    --card: #ffffff;
    --navy: #262d6e;
    --yellow: #f5c21b;
    --ink: #1f1f1f;
    --grey: #5d5d5d;
  }
  * { box-sizing: border-box; margin: 0; padding: 0; }
  html, body { width: 1200px; height: 1200px; overflow: hidden; }
  body { background: var(--bg); position: relative; font-family: "Roboto", Arial, sans-serif; }

  .heading {
    position: absolute; left: 0; width: 1200px; top: 240px; text-align: center;
    font-family: "Raleway", Arial, sans-serif; font-size: 35px; color: var(--navy);
    font-weight: 500; letter-spacing: 0.5px;
  }
  .heading strong { font-weight: 700; }

  .signature {
    position: absolute; left: 259px; width: 682px; height: 238px;
    background: var(--card); box-shadow: 6px 7px 8px rgba(0,0,0,0.28);
  }
  .signature--wide { top: 336px; }
  .signature--split { top: 626px; }

  .brand { position: absolute; width: 220px; text-align: center; }
  .brand__mark { width: 40px; height: 40px; border-radius: 50%; background: var(--navy); margin: 0 auto 12px; }
  .brand__name { font-weight: 700; font-size: 29px; line-height: 30px; color: var(--ink); }

  .contact { position: absolute; }
  .contact__name { font-weight: 700; font-size: 19px; color: var(--navy); line-height: 22px; letter-spacing: 0.2px; }
  .contact__role { font-size: 16px; color: var(--yellow); line-height: 20px; }
  .contact__address { font-size: 14.5px; color: var(--grey); line-height: 18px; }
  .contact__list { list-style: none; font-size: 14.5px; color: var(--grey); line-height: 19px; margin-top: 7px; }
  .contact__list li { display: flex; align-items: center; gap: 6px; }
  .contact__list svg { width: 13px; height: 13px; fill: var(--navy); flex: none; }

  .rule-h { position: absolute; height: 1.5px; background: var(--yellow); }
  .rule-v { position: absolute; width: 1.5px; background: var(--yellow); }

  .social { position: absolute; display: flex; gap: 5px; }
  .social span { width: 20px; height: 20px; border-radius: 50%; border: 1.5px solid var(--navy); }
</style>
</head>
<body>
  <h1 class="heading"><strong>CLICKABLE&nbsp; HTML</strong> EMAIL SIGNATURE</h1>

  <section class="signature signature--wide">
    <div class="brand" style="left:31px; top:62px;">
      <div class="brand__mark"></div>
      <div class="brand__name">Maple Grove<br>Schools</div>
    </div>
    <div class="contact" style="left:292px; top:35px;">
      <div class="contact__name">DANIEL R. WHITFIELD</div>
      <div class="contact__role">Founder &amp; CEO</div>
    </div>
    <div class="rule-h" style="left:292px; top:88px; width:390px;"></div>
    <div class="contact" style="left:292px; top:103px;">
      <div class="contact__address">48 Elm Avenue, Suite 3<br>Carverton, MA 01920</div>
      <ul class="contact__list">
        <li><svg viewBox="0 0 16 16"><path d="M3.5 1l2.6 3-1.5 2a9 9 0 0 0 4.9 4.9l2-1.5 3 2.6-1.4 2.4C7.5 14.8 1.2 8.5 1.1 2.4z"/></svg>(555) 318-4702</li>
        <li><svg viewBox="0 0 16 16"><path d="M1 3h14v10H1zm1.5 1.5v.3L8 9l5.5-4.2v-.3zm0 2.2v4.8h11V6.7L8 10.9z"/></svg>office@maplegrove.edu</li>
        <li><svg viewBox="0 0 16 16"><path d="M8 1a7 7 0 1 0 0 14A7 7 0 0 0 8 1zm0 1.3c.8.9 1.4 2.3 1.6 4H6.4C6.6 4.6 7.2 3.2 8 2.3zM2.4 7.3h2.7c0 .5 0 .9.1 1.4H2.4a5.6 5.6 0 0 1 0-1.4zm4 0h3.2a9 9 0 0 1 0 1.4H6.4a9 9 0 0 1 0-1.4zm4.5 0h2.7a5.6 5.6 0 0 1 0 1.4h-2.7c.1-.5.1-.9 0-1.4zM6.4 9.7h3.2c-.2 1.7-.8 3.1-1.6 4-.8-.9-1.4-2.3-1.6-4z"/></svg>www.maplegrove.edu</li>
      </ul>
    </div>
    <div class="social" style="left:536px; top:181px;" aria-label="Social links">
      <span></span><span></span><span></span><span></span>
    </div>
  </section>

  <section class="signature signature--split">
    <div class="social" style="left:34px; top:30px;" aria-label="Social links">
      <span></span><span></span><span></span><span></span>
    </div>
    <div class="brand" style="left:111px; top:62px;">
      <div class="brand__mark"></div>
      <div class="brand__name">Maple Grove<br>Schools</div>
    </div>
    <div class="rule-v" style="left:336px; top:36px; height:166px;"></div>
    <div class="contact" style="left:368px; top:35px;">
      <div class="contact__name">DANIEL R. WHITFIELD</div>
      <div class="contact__role">Founder &amp; CEO</div>
    </div>
    <div class="contact" style="left:368px; top:105px;">
      <div class="contact__address">48 Elm Avenue, Suite 3<br>Carverton, MA 01920</div>
      <ul class="contact__list">
        <li><svg viewBox="0 0 16 16"><path d="M3.5 1l2.6 3-1.5 2a9 9 0 0 0 4.9 4.9l2-1.5 3 2.6-1.4 2.4C7.5 14.8 1.2 8.5 1.1 2.4z"/></svg>(555) 318-4702</li>
        <li><svg viewBox="0 0 16 16"><path d="M1 3h14v10H1zm1.5 1.5v.3L8 9l5.5-4.2v-.3zm0 2.2v4.8h11V6.7L8 10.9z"/></svg>office@maplegrove.edu</li>
        <li><svg viewBox="0 0 16 16"><path d="M8 1a7 7 0 1 0 0 14A7 7 0 0 0 8 1zm0 1.3c.8.9 1.4 2.3 1.6 4H6.4C6.6 4.6 7.2 3.2 8 2.3zM2.4 7.3h2.7c0 .5 0 .9.1 1.4H2.4a5.6 5.6 0 0 1 0-1.4zm4 0h3.2a9 9 0 0 1 0 1.4H6.4a9 9 0 0 1 0-1.4zm4.5 0h2.7a5.6 5.6 0 0 1 0 1.4h-2.7c.1-.5.1-.9 0-1.4zM6.4 9.7h3.2c-.2 1.7-.8 3.1-1.6 4-.8-.9-1.4-2.3-1.6-4z"/></svg>www.maplegrove.edu</li>
      </ul>
    </div>
  </section>
</body>
</html>
```